Coastline Premier Retreats Business Card Design

Design a business card for Coastline Premier Retreats. Look at the website for colors and reference. Card should have logo, name, title, office number, mobile number, email, URL and a tagline like, "Luxury Hotel & Resort Email Marketing" (This might change).

https://www.coastlinepremierretreats.example

The rest I will leave up to your imagination.

Contact Information for Business Card

Logo, name, title, office number, mobile number, email, URL and a tagline like, "Luxury Hotel & Resort Email Marketing" (This might change).

```html
<!DOCTYPE html>
<html lang="en">
<head>
<meta charset="utf-8">
<title>Coastline Premier Retreats – Business Card</title>
<link href="https://fonts.googleapis.com/css2?family=Montserrat:wght@400;500;700;800&display=swap" rel="stylesheet">
<style>
  :root {
    --backdrop: #d3d7d7;
    --paper: #fbfbfa;
    --brand-orange: #e86f17;
    --ink: #1c1c1c;
    --muted: #3a3a3a;
    --on-orange: #f7f3ee;
  }
  * { box-sizing: border-box; margin: 0; padding: 0; }
  html, body { width: 1200px; height: 829px; overflow: hidden; }
  body {
    background: var(--backdrop);
    font-family: "Montserrat", sans-serif;
    position: relative;
  }
  .card {
    position: absolute;
    top: 265px;
    width: 525px;
    height: 300px;
    border-radius: 3px;
    overflow: hidden;
    box-shadow: 0 14px 30px rgba(0,0,0,0.18);
  }
  /* Front */
  .card-front { left: 50px; background: var(--paper); }
  .holder-block { position: absolute; left: 34px; top: 58px; }
  .holder-name {
    color: var(--brand-orange); font-weight: 800; font-size: 24px; letter-spacing: 0.5px; line-height: 28px;
  }
  .holder-title { color: var(--muted); font-size: 12px; margin-top: 2px; }
  .divider {
    position: absolute; left: 34px; right: 34px; top: 126px;
    height: 1px; background: var(--brand-orange);
  }
  .contact-list {
    position: absolute; left: 34px; top: 140px; list-style: none;
    font-size: 11.5px; color: var(--muted); line-height: 21px;
  }
  .contact-list li { display: flex; align-items: center; gap: 8px; }
  .contact-list svg { width: 10px; height: 10px; fill: var(--brand-orange); }
  .front-brand {
    position: absolute; right: 34px; top: 62px; width: 190px;
    display: flex; align-items: center; gap: 10px;
    color: var(--ink); font-weight: 700; font-size: 15px; line-height: 19px;
    text-transform: uppercase; letter-spacing: 0.5px;
  }
  .brand-square { flex: none; width: 14px; height: 14px; background: var(--brand-orange); }
  .address {
    position: absolute; right: 34px; top: 204px; text-align: right;
    font-size: 11.5px; color: var(--muted); line-height: 17px;
  }
  .footer-band { position: absolute; left: 0; bottom: 0; width: 525px; height: 46px; }
  .web-url {
    position: absolute; right: 22px; bottom: 9px;
    font-size: 11.5px; color: #fff;
  }
  .web-url .domain { color: var(--brand-orange); }
  /* Back */
  .card-back { left: 625px; background: var(--brand-orange); }
  .back-brand {
    position: absolute; left: 0; right: 0; top: 112px;
    display: flex; justify-content: center; align-items: center; gap: 10px;
    color: var(--on-orange); font-weight: 700; font-size: 22px; text-transform: uppercase; letter-spacing: 1px;
  }
  .back-brand .brand-square { background: var(--on-orange); width: 16px; height: 16px; }
  .tagline {
    position: absolute; left: 0; right: 0; top: 168px; text-align: center;
    color: var(--on-orange); font-size: 12.5px; letter-spacing: 0.3px;
  }
</style>
</head>
<body>
  <section class="card card-front" aria-label="Business card front">
    <div class="holder-block">
      <h1 class="holder-name">DANIEL HART</h1>
      <p class="holder-title">CEO/Founder</p>
    </div>
    <div class="front-brand"><span class="brand-square"></span><span>Coastline Premier Retreats</span></div>
    <div class="divider"></div>
    <ul class="contact-list">
      <li><svg viewBox="0 0 10 10"><rect x="2.5" y="0" width="5" height="10" rx="1"/></svg>555.014.2200</li>
      <li><svg viewBox="0 0 10 10"><path d="M2 0 L4 3 L3 4 Q4 6 6 7 L7 6 L10 8 L8 10 Q2 9 0 2 Z"/></svg>+34 600 555 217</li>
      <li><svg viewBox="0 0 10 10"><path d="M0 2 H10 V9 H0 Z M0 2 L5 6 L10 2" stroke="#fbfbfa" stroke-width="0.8"/></svg>info@coastlinepremierretreats.example</li>
    </ul>
    <p class="address">Po Box, 456 Harbor Rd<br>Seaside Bay, CA 90210</p>
    <svg class="footer-band" viewBox="0 0 525 46" preserveAspectRatio="none">
      <path d="M0 22 H214 Q226 22 231 16 L235 18 Q229 26 216 26 H0 Z" fill="var(--brand-orange)"/>
      <path d="M0 32 H216 Q232 32 238 22 Q243 12 260 12 H525 V46 H0 Z" fill="var(--ink)"/>
    </svg>
    <p class="web-url">www.<span class="domain">coastlinepremierretreats</span>.example</p>
  </section>

  <section class="card card-back" aria-label="Business card back">
    <div class="back-brand"><span class="brand-square"></span>Coastline Premier Retreats</div>
    <p class="tagline">Luxury Hotel &amp; Resort Email Marketing</p>
  </section>
</body>
</html>
```